Acupuncture business needs business card design

I need a business card for an acupuncture clinic called "Harbourlight Wellness"
It will need the following details:
My name: Marcus Pelling
Acupuncturist
Member TVBH
KWF Treatment Provider
Ph numbers: 581 2734 027 418 5620
Email: marcus@hbwel.example.nz
On the back it will need a table with 2 columns for appointments, one column for time and one for date.

Industry/Entity Type

Clinic

Contact Information for Business Card

Marcus Pelling
Acupuncturist
Member TVBH
KWF Treatment Provider
Email: marcus@hbwel.example.nz

Requirements
Must have
• Marcus Pelling
• Acupuncturist
• Member TVBH
• KWF Treatment Provider
• Ph numbers: 581 2734 027 418 5620
• Email: marcus@hbwel.example.nz
• On the back it will need a table with 2 columns for appointments, one column for time and one for date.

```html
<!DOCTYPE html>
<html lang="en">
<head>
<meta charset="utf-8">
<title>Harbourlight Wellness – Business Card</title>
<link rel="stylesheet" href="https://fonts.googleapis.com/css2?family=Open+Sans:wght@400;600;700&display=swap">
<style>
  :root {
    --page-bg: #e9ecee;
    --card-bg: #ffffff;
    --brand-blue: #1ba3cc;
    --brand-blue-light: #7fcbe2;
    --brand-grey: #6f8b96;
    --ink-dark: #1d4f63;
    --ink-soft: #3a93b5;
    --rule: #6d6d6d;
    --label: #444444;
  }
  * { box-sizing: border-box; margin: 0; padding: 0; }
  html, body {
    width: 1200px; height: 948px; overflow: hidden;
    background: var(--page-bg);
    font-family: "Open Sans", Arial, sans-serif;
  }
  .sheet {
    position: relative; width: 1200px; height: 948px;
    display: flex; align-items: center; justify-content: center; gap: 40px;
  }
  .card {
    position: relative; width: 540px; height: 308px;
    background: var(--card-bg);
    box-shadow: 0 6px 18px rgba(0,0,0,0.15);
    overflow: hidden;
  }
  .card-band { position: absolute; left: 0; top: 0; width: 540px; height: 120px; }

  .brand { position: absolute; display: flex; align-items: center; gap: 10px; }
  .brand-dot {
    width: 30px; height: 30px; border-radius: 50%;
    background: var(--brand-blue); flex: none;
  }
  .brand-name {
    font-weight: 700; color: var(--brand-blue);
    font-size: 27px; line-height: 1; letter-spacing: -0.3px;
  }
  .brand-tagline {
    margin-top: 4px; font-size: 9.5px; letter-spacing: 3.6px;
    color: var(--brand-grey); text-transform: uppercase;
  }

  /* front */
  .card-front .brand { left: 196px; top: 66px; }
  .contact { position: absolute; left: 34px; top: 150px; }
  .contact-name { font-weight: 700; font-size: 15px; color: var(--ink-dark); }
  .contact-role { font-size: 11.5px; color: var(--ink-soft); line-height: 1.45; }
  .contact-lines { margin-top: 14px; }
  .contact-line {
    display: flex; align-items: center; gap: 8px;
    font-size: 12px; color: #333; margin-bottom: 7px;
  }
  .contact-icon {
    width: 15px; height: 15px; border-radius: 50%;
    background: var(--brand-blue); display: flex; align-items: center; justify-content: center;
  }

  /* back */
  .card-back .brand { left: 34px; top: 28px; }
  .appointments {
    position: absolute; left: 34px; top: 100px;
    border-collapse: separate; border-spacing: 6px 5px;
    margin-left: -6px;
  }
  .appointments th {
    font-weight: 400; font-size: 13px; color: var(--label);
    text-align: left; padding: 0 2px 2px;
  }
  .appointments td {
    border: 1px solid var(--rule); height: 26px;
  }
  .appointments .col-date { width: 250px; }
  .appointments .col-time { width: 200px; }
  .web {
    position: absolute; left: 34px; bottom: 22px;
    font-size: 13px; letter-spacing: 2.4px; color: var(--label);
  }
</style>
</head>
<body>
<main class="sheet">

  <section class="card card-front" aria-label="Business card front">
    <svg class="card-band" viewBox="0 0 540 120" aria-hidden="true">
      <polygon points="0,0 250,0 0,70" fill="var(--brand-blue)"/>
      <polygon points="250,0 300,0 0,86 0,70" fill="var(--brand-blue-light)"/>
    </svg>

    <div class="brand">
      <span class="brand-dot"></span>
      <div>
        <div class="brand-name">Harbourlight Wellness</div>
        <div class="brand-tagline">Acupuncture Physiotherapy</div>
      </div>
    </div>

    <div class="contact">
      <div class="contact-name">Marcus Pelling</div>
      <div class="contact-role">Acupuncturist Member TVBH<br>KWF Treatment Provider</div>
      <div class="contact-lines">
        <div class="contact-line">
          <span class="contact-icon">
            <svg width="9" height="9" viewBox="0 0 24 24"><path fill="#fff" d="M6.6 10.8a15.1 15.1 0 0 0 6.6 6.6l2.2-2.2a1 1 0 0 1 1-.25 11.4 11.4 0 0 0 3.6.57 1 1 0 0 1 1 1V20a1 1 0 0 1-1 1A17 17 0 0 1 3 4a1 1 0 0 1 1-1h3.5a1 1 0 0 1 1 1c0 1.25.2 2.45.57 3.57a1 1 0 0 1-.25 1z"/></svg>
          </span>
          581 2734 · 027 418 5620
        </div>
        <div class="contact-line">
          <span class="contact-icon">
            <svg width="9" height="9" viewBox="0 0 24 24"><path fill="#fff" d="M2 5h20v14H2z"/><path fill="none" stroke="var(--brand-blue)" stroke-width="2" d="M2 5l10 8 10-8"/></svg>
          </span>
          marcus@hbwel.example.nz
        </div>
      </div>
    </div>
  </section>

  <section class="card card-back" aria-label="Business card back">
    <div class="brand">
      <span class="brand-dot"></span>
      <div>
        <div class="brand-name">Harbourlight Wellness</div>
        <div class="brand-tagline">Acupuncture Physiotherapy</div>
      </div>
    </div>

    <table class="appointments">
      <thead>
        <tr><th>Date</th><th>Time</th></tr>
      </thead>
      <tbody>
        <tr><td class="col-date"></td><td class="col-time"></td></tr>
        <tr><td class="col-date"></td><td class="col-time"></td></tr>
        <tr><td class="col-date"></td><td class="col-time"></td></tr>
      </tbody>
    </table>

    <div class="web">www.hbwel.example.nz</div>
  </section>

</main>
</body>
</html>
```